Maple Lantern Productions web site

I need to build a website for a new company I am launching next month. Maple Lantern Productions is a company based in New England that provides sound, lighting, and audio visual services to weddings, corporate, and any other cusomer base looking for quality service for a fair price. Looking for somebody to do a full site not just the image files. I am looking to keep the colors of my logo (orange and black) and possibly grey and white. I am looking to build my site very similar to brightvaleevents.example, which is owned by a friend of mine. I like how he has the big pictures that load in to the site and the basic menu items. I'll need a gallery of photos. The designs should communicate quality, value and trust.
My website address is maplelanternco.example.
Updates

Hi and thanks to everyone for posting such great ideas for our new design.I have some items that I'd like to ask you all to focus on in your revisions.I like how http://www.brightvaleevents.example/ website has five or six high res pictures that change in a slideshow format with a caption that loads in for each one for the different types of services. Try and capture pics like these and with teh same headings as he has. The basic menu designs have been interesting.I am more fond of the menus that are more white with some orange as I dont want it to be too dark. I'm curious to see how your galleries will work and if i'll be able to edit the pages myself? I have some more info on the company for you to fill in:website address is ciderhouseco.comemail: info@ciderhouseco.comaddress: Maple Lantern Productions57 Littlefield StreetAvon, MA 02417"New England's finest DJ's, lighting and sound, video and more. Creating memories one perfect event at a time."Put this under the loading pictures as a tagline.About Cider HouseCider House Productions is a collection of New England's finest talent, ready to make your next event the one you've dreamed of. We have the skills and expertise to deliver your vision of your perfect event. From elegant weddings to themed mitzvah's, corporate av, videography and detail lighting, we offer all of the elements to make your event a success. Added Wednesday, March 1, 2017

Designer's Please also make sure that your design flows well on any device it is being viewed on as well. Thanks. Added Wednesday, March 1, 2017

Project Deadline Extended Reason: Hello designerThank you all very much for your hard work on our project. Im sorry but i need to extend the date of my project. Our parent conpany Rook Nine Prodactions sponsors Bay Youth Assemblies and we are currently at their leadership conference on the Cape. I will be back in on Monday and with your help will get this finished by Thursday the 16th. Thanks Added Thursday, March 9, 2017

Project Deadline Extended Reason: One of the designers is not responding so I now have to make revisions with other designers. I hope to get this website done over the weekends so please get your revisions as soon as possible. Thank you. I am also upgrading the budget another $75 to hopefully get some more interest on my project. Added Wednesday, March 15, 2017

Target Market(s)

Wedding - Corporate -

Industry/Entity Type

It Company

Coding

Coded - Design and coding required

Number of Pages Required

5+ page

Font styles to use
Sans Serif

Requirements
Must have
• Photo Gallery - I want to be able to edit it myself
Nice to have
• I like the look of my friends website brightvaleevents.example

```html
<!DOCTYPE html>
<html lang="en">
<head>
<meta charset="utf-8">
<title>Maple Lantern Productions</title>
<link rel="stylesheet" href="https://fonts.googleapis.com/css2?family=Open+Sans:wght@400;600;700&display=swap">
<style>
:root{
  --orange:#ee5a26;
  --orange-dark:#d84a1a;
  --ink:#222222;
  --text:#555555;
  --muted:#888888;
  --line:#e2e2e2;
  --grey-bg:#f2f2f2;
  --footer:#2b2b2b;
  --white:#ffffff;
}
*{box-sizing:border-box;margin:0;padding:0}
html,body{width:1200px;height:4412px;overflow:hidden}
body{font-family:"Open Sans",Arial,sans-serif;color:var(--text);background:var(--white);position:relative}
.wrap{position:absolute;left:132px;width:936px}
.section-title{text-align:center;color:var(--orange);font-size:24px;font-weight:600;letter-spacing:1px;text-transform:uppercase}
.lead{text-align:center;font-size:12.5px;line-height:21px;color:var(--text)}
.btn-outline{display:inline-block;border:1px solid #cfcfcf;color:#777;font-size:12px;padding:8px 16px;background:var(--white)}

/* header */
.site-header{position:absolute;top:0;left:0;width:1200px;height:124px;background:var(--white);box-shadow:0 1px 3px rgba(0,0,0,.08)}
.brand{position:absolute;left:132px;top:22px;display:flex;align-items:center;gap:14px}
.brand-dot{width:76px;height:76px;border-radius:50%;background:var(--orange)}
.brand-name{font-size:25px;font-weight:700;color:var(--ink);line-height:28px;letter-spacing:.5px}
.brand-name span{display:block;font-size:14px;letter-spacing:4px;font-weight:700;color:var(--ink)}
.contact-bar{position:absolute;right:132px;top:20px;display:flex;gap:26px;font-size:15px;font-weight:600;color:var(--ink)}
.contact-bar span{display:flex;align-items:center;gap:8px}
.main-nav{position:absolute;right:132px;top:82px;display:flex;gap:24px;font-size:12.5px;color:var(--ink)}
.main-nav .active{color:var(--orange)}

/* hero */
.hero{position:absolute;top:124px;left:0;width:1200px;height:491px;
  background:radial-gradient(circle at 70% 20%,#3a8fb0 0,transparent 18%),radial-gradient(circle at 25% 80%,#c23c6c 0,transparent 30%),radial-gradient(circle at 85% 75%,#b02a5a 0,transparent 25%),linear-gradient(160deg,#1b1030 0%,#3b1d55 45%,#5a1c3c 75%,#1a0f20 100%)}
.hero-caption{position:absolute;top:178px;left:0;width:1200px;text-align:center;color:var(--white)}
.hero-caption h1{font-size:33px;font-weight:700;letter-spacing:1px;text-transform:uppercase;text-shadow:0 2px 6px rgba(0,0,0,.5)}
.hero-caption p{font-size:20px;font-weight:600;margin-top:4px;text-shadow:0 2px 6px rgba(0,0,0,.5)}
.hero-caption .btn-hero{display:inline-block;margin-top:16px;border:2px solid var(--white);padding:8px 20px;font-size:19px;font-weight:600}
.hero-arrow{position:absolute;top:232px}

/* welcome */
.welcome{top:690px}
.welcome .lead{margin-top:14px}
.services{position:absolute;top:845px;left:132px;width:936px;display:flex;justify-content:space-between}
.service{width:220px;text-align:center}
.service-icon{width:82px;height:82px;border-radius:50%;background:var(--orange);margin:0 auto;display:flex;align-items:center;justify-content:center}
.service h3{font-size:21px;font-weight:700;color:var(--ink);margin-top:12px;letter-spacing:1px}
.service p{font-size:11px;line-height:16px;margin-top:4px}
.divider{position:absolute;top:1082px;left:0;width:1200px;border-top:1px solid var(--line)}

/* events */
.event{position:absolute;left:132px;width:936px;height:256px}
.event-photo{position:absolute;top:0;width:448px;height:256px}
.event-body{position:absolute;top:16px;width:448px}
.event-body h2{font-size:31px;font-weight:400;color:var(--ink)}
.event-body p{font-size:12px;line-height:20px;margin:12px 0 16px}
.event.right .event-photo{left:0}
.event.right .event-body{left:485px}
.event.left .event-photo{left:485px}
.event.left .event-body{left:0}

/* team */
.team{position:absolute;top:2508px;left:0;width:1200px;height:441px;background:var(--grey-bg)}
.team .section-title{position:absolute;top:75px;width:1200px}
.team .lead{position:absolute;top:110px;left:132px;width:936px}
.team-grid{position:absolute;top:176px;left:132px;width:936px;display:flex;justify-content:space-between}
.member{width:176px;height:182px;background:var(--white);border:1px solid var(--line);padding:8px;text-align:center}
.member-photo{width:158px;height:134px;background:linear-gradient(180deg,#d9d9d9,#b9b9b9)}
.member-name{font-size:11px;color:var(--muted);margin-top:12px}

/* testimonials */
.testimonials .section-title{position:absolute;top:3022px;width:1200px}
.quote-box{position:absolute;top:3075px;left:270px;width:644px;height:165px;border:1px solid #d6d6d6;background:var(--white);text-align:center;padding:28px 50px}
.quote-box p{font-size:12.5px;line-height:20px;color:var(--text)}
.quote-box .by{margin-top:10px;font-size:12.5px}
.quote-mark{font-size:30px;color:var(--ink);font-weight:700;line-height:0;vertical-align:-8px}
.quote-avatar{position:absolute;top:3215px;left:570px;width:54px;height:54px;border-radius:50%;background:#c8c8c8;border:4px solid var(--white);box-shadow:0 0 0 1px var(--line)}
.quote-side{position:absolute;top:3075px;width:132px;height:165px;background:linear-gradient(90deg,#f4f4f4,#e9e9e9)}

/* gallery */
.gallery .section-title{position:absolute;top:3345px;width:1200px}
.gallery-arrow{position:absolute;top:3353px}
.gallery-grid{position:absolute;top:3401px;left:132px;width:936px;display:grid;grid-template-columns:repeat(4,216px);grid-auto-rows:215px;column-gap:24px;row-gap:24px}

/* contact */
.contact{position:absolute;top:3940px;left:0;width:1200px;height:373px;background:var(--grey-bg)}
.contact .section-title{position:absolute;top:40px;width:1200px}
.contact-form{position:absolute;top:108px;left:132px;width:936px}
.form-row{display:flex;justify-content:space-between;margin-bottom:20px}
.field{width:216px;height:40px;background:var(--white);border:1px solid #d9d9d9;font-size:11px;color:#999;padding:0 12px;display:flex;align-items:center;justify-content:space-between}
.field.wide{width:936px}
.submit{display:block;margin:0 auto;width:80px;height:38px;background:var(--ink);color:var(--white);font-size:12px;font-weight:700;border:none;font-family:inherit}

/* footer */
.site-footer{position:absolute;top:4313px;left:0;width:1200px;height:99px;background:var(--footer);color:#bbbbbb}
.footer-nav{position:absolute;top:30px;left:132px;font-size:11px;display:flex;gap:10px}
.copyright{position:absolute;top:56px;left:132px;font-size:11px}
.social{position:absolute;top:30px;right:132px;display:flex;gap:10px}
.social span{width:32px;height:32px;border:1px solid #777;border-radius:50%}
</style>
</head>
<body>

<header class="site-header">
  <div class="brand">
    <div class="brand-dot"></div>
    <div class="brand-name">MAPLE LANTERN<span>PRODUCTIONS</span></div>
  </div>
  <div class="contact-bar">
    <span><svg width="12" height="14" viewBox="0 0 12 14"><rect x="2" y="0" width="8" height="14" rx="1.5" fill="#222"/><rect x="3.5" y="2" width="5" height="8" fill="#fff"/></svg>555 014 2298</span>
    <span><svg width="16" height="12" viewBox="0 0 16 12"><rect width="16" height="12" rx="1" fill="#222"/><path d="M1 1l7 6 7-6" stroke="#fff" stroke-width="1.4" fill="none"/></svg>info@maplelanternco.example</span>
  </div>
  <nav class="main-nav">
    <span class="active">Home</span><span>About Us</span><span>Services</span><span>Gallery</span><span>Testimonials</span><span>Events</span><span>Check Availability</span><span>Contact Us</span>
  </nav>
</header>

<section class="hero" role="img" aria-label="Dance floor under colourful stage lights at a night event">
  <svg class="hero-arrow" style="left:8px" width="16" height="24" viewBox="0 0 16 24"><path d="M12 3L4 12l8 9" stroke="#fff" stroke-width="2" fill="none"/></svg>
  <svg class="hero-arrow" style="right:8px" width="16" height="24" viewBox="0 0 16 24"><path d="M4 3l8 9-8 9" stroke="#fff" stroke-width="2" fill="none"/></svg>
  <div class="hero-caption">
    <h1>Etiam faucibus imperdiet consequat nulla</h1>
    <p>Morbi ultrices sem vel augue sollicitudin dolor accumsan</p>
    <span class="btn-hero">Check Availability</span>
  </div>
</section>

<section class="wrap welcome">
  <h2 class="section-title">Welcome to Maple Lantern Productions</h2>
  <p class="lead">Maple Lantern Productions brings together talented DJs, lighting designers and sound engineers from across New England. We plan every detail with you, arrive early, test twice and stay until the last guest leaves. From intimate ceremonies to large corporate gatherings, our crew delivers clear sound, warm light and smooth visuals at a fair price, so you can relax and enjoy the moment with the people who matter most.</p>
</section>

<div class="services">
  <div class="service">
    <div class="service-icon"><svg width="34" height="30" viewBox="0 0 34 30"><path d="M2 10h6l9-8v26l-9-8H2z" fill="#fff"/><path d="M22 9a8 8 0 010 12M26 5a13 13 0 010 20" stroke="#fff" stroke-width="2.5" fill="none"/></svg></div>
    <h3>SOUND</h3>
    <p>Crisp, balanced audio sized for your room, with wireless mics and an engineer on site.</p>
  </div>
  <div class="service">
    <div class="service-icon"><svg width="26" height="34" viewBox="0 0 26 34"><path d="M13 2a11 11 0 00-6 20v4h12v-4a11 11 0 00-6-20z" fill="#fff"/><rect x="8" y="28" width="10" height="3" fill="#fff"/></svg></div>
    <h3>LIGHTING</h3>
    <p>Uplighting, dance floor effects and soft washes that set the mood for every moment.</p>
  </div>
  <div class="service">
    <div class="service-icon"><svg width="30" height="30" viewBox="0 0 30 30"><g stroke="#fff" stroke-width="2.5"><path d="M6 2v26M15 2v26M24 2v26"/></g><g fill="#fff"><rect x="2" y="17" width="8" height="5" rx="1"/><rect x="11" y="7" width="8" height="5" rx="1"/><rect x="20" y="14" width="8" height="5" rx="1"/></g></svg></div>
    <h3>AUDIO VISUAL</h3>
    <p>Projectors, screens and video playback handled cleanly for talks, toasts and shows.</p>
  </div>
</div>
<div class="divider"></div>

<article class="event right" style="top:1161px">
  <div class="event-photo" role="img" aria-label="Wedding reception hall with draped ceiling and chandelier in pink and purple light" style="background:linear-gradient(135deg,#e9a4d8,#b25bb0 50%,#d98fc7)"></div>
  <div class="event-body">
    <h2>Weddings</h2>
    <p>Your wedding deserves music and light that feel personal. We meet with you ahead of time to plan the ceremony, first dance and reception flow, then shape the room with soft colour and clear sound so every toast is heard and the dance floor stays full all evening long.</p>
    <span class="btn-outline">View Packages</span>
  </div>
</article>

<article class="event left" style="top:1499px">
  <div class="event-photo" role="img" aria-label="Child celebrating with a birthday cake and candles" style="background:linear-gradient(135deg,#2a4f8a,#c0442a 50%,#e9b24a)"></div>
  <div class="event-body">
    <h2>Birthday Parties</h2>
    <p>From a first birthday to a fiftieth, we bring the right music, games and lighting for every age. Our DJs read the crowd, keep the energy high and make sure the cake moment gets its spotlight. Setup is quick, tidy and safe for homes, halls and backyards across the region.</p>
    <span class="btn-outline">View Packages</span>
  </div>
</article>

<article class="event right" style="top:1834px">
  <div class="event-photo" role="img" aria-label="Auditorium full of students facing a lit stage" style="background:linear-gradient(135deg,#6b3a22,#b0683a 50%,#3a2218)"></div>
  <div class="event-body">
    <h2>School and Formal Events</h2>
    <p>Proms, graduations and school dances run best with a partner who knows the rules. We provide clean playlists, clear announcements and bright stage lighting, and we work closely with staff and student councils to keep the night fun, safe and running right on schedule.</p>
    <span class="btn-outline">View Packages</span>
  </div>
</article>

<article class="event left" style="top:2170px">
  <div class="event-photo" role="img" aria-label="Presenter at a corporate conference with an audience in the background" style="background:linear-gradient(135deg,#cfc9c2,#8a8079 50%,#3a3330)"></div>
  <div class="event-body">
    <h2>Corporate Events</h2>
    <p>Conferences, product launches and holiday parties call for reliable audio visual support. We handle microphones, projection, stage wash and background music with a calm, professional crew, so your speakers sound confident and your guests stay focused on the message.</p>
    <span class="btn-outline">View Packages</span>
  </div>
</article>

<section class="team">
  <h2 class="section-title">About Our Team</h2>
  <p class="lead">Our crew is made up of experienced DJs, lighting techs and AV specialists who love live events. Each member is trained on our own gear and focused on one goal: making your night run smoothly from the first song to the final farewell.</p>
  <div class="team-grid">
    <div class="member"><div class="member-photo" role="img" aria-label="Team member portrait"></div><div class="member-name">Alex Moore</div></div>
    <div class="member"><div class="member-photo" role="img" aria-label="Team member portrait"></div><div class="member-name">Alex Moore</div></div>
    <div class="member"><div class="member-photo" role="img" aria-label="Team member portrait"></div><div class="member-name">Alex Moore</div></div>
    <div class="member"><div class="member-photo" role="img" aria-label="Team member portrait"></div><div class="member-name">Alex Moore</div></div>
    <div class="member"><div class="member-photo" role="img" aria-label="Team member portrait"></div><div class="member-name">Alex Moore</div></div>
  </div>
</section>

<section class="testimonials">
  <h2 class="section-title">Testimonials</h2>
  <div class="quote-side" style="left:132px"><svg style="position:absolute;left:6px;top:72px" width="12" height="20" viewBox="0 0 12 20"><path d="M10 2L3 10l7 8" stroke="#bbb" stroke-width="2" fill="none"/></svg></div>
  <div class="quote-side" style="left:936px"><svg style="position:absolute;right:6px;top:72px" width="12" height="20" viewBox="0 0 12 20"><path d="M2 2l7 8-7 8" stroke="#bbb" stroke-width="2" fill="none"/></svg></div>
  <div class="quote-box">
    <p><span class="quote-mark">&ldquo;</span> From the first phone call to the last dance, the team was friendly, prepared and professional. The lighting transformed our hall and the dance floor stayed full all night. We would book them again without a second thought. <span class="quote-mark">&rdquo;</span></p>
    <p class="by">&mdash; Alex Moore</p>
  </div>
  <div class="quote-avatar" role="img" aria-label="Client portrait"></div>
</section>

<section class="gallery">
  <svg class="gallery-arrow" style="left:132px" width="18" height="14" viewBox="0 0 18 14"><path d="M17 7H2M7 1L1 7l6 6" stroke="#666" stroke-width="1.6" fill="none"/></svg>
  <svg class="gallery-arrow" style="right:132px" width="18" height="14" viewBox="0 0 18 14"><path d="M1 7h15M11 1l6 6-6 6" stroke="#666" stroke-width="1.6" fill="none"/></svg>
  <h2 class="section-title">Gallery</h2>
  <div class="gallery-grid">
    <div role="img" aria-label="DJ at a mixing desk" style="background:linear-gradient(135deg,#2b3d6b,#b8433a)"></div>
    <div role="img" aria-label="Ceiling projector" style="background:linear-gradient(135deg,#e6e6e6,#7a7a7a)"></div>
    <div role="img" aria-label="Blue stage beams over a crowd" style="background:linear-gradient(135deg,#0a1a2e,#3fa6d8)"></div>
    <div role="img" aria-label="Children singing together" style="background:linear-gradient(135deg,#d8c3b2,#8a5a4a)"></div>
    <div role="img" aria-label="Concert crowd under orange lights" style="background:linear-gradient(135deg,#f2a22a,#5a1a0a)"></div>
    <div role="img" aria-label="Colourful party lights" style="background:linear-gradient(135deg,#d33a8a,#2a6ad8)"></div>
    <div role="img" aria-label="Close-up of a loudspeaker" style="background:linear-gradient(135deg,#d0d0d0,#1a1a1a)"></div>
    <div role="img" aria-label="Guitarist on stage" style="background:linear-gradient(135deg,#2a1a4a,#c0447a)"></div>
  </div>
</section>

<section class="contact">
  <h2 class="section-title">Contact Us</h2>
  <form class="contact-form">
    <div class="form-row">
      <div class="field">Name</div><div class="field">Email</div><div class="field">Phone</div>
      <div class="field">Service for <svg width="8" height="5" viewBox="0 0 8 5"><path d="M0 0h8L4 5z" fill="#666"/></svg></div>
    </div>
    <div class="form-row">
      <div class="field">Event Type <svg width="8" height="5" viewBox="0 0 8 5"><path d="M0 0h8L4 5z" fill="#666"/></svg></div>
      <div class="field">Month <svg width="8" height="5" viewBox="0 0 8 5"><path d="M0 0h8L4 5z" fill="#666"/></svg></div>
      <div class="field">Date <svg width="8" height="5" viewBox="0 0 8 5"><path d="M0 0h8L4 5z" fill="#666"/></svg></div>
      <div class="field">Year <svg width="8" height="5" viewBox="0 0 8 5"><path d="M0 0h8L4 5z" fill="#666"/></svg></div>
    </div>
    <div class="form-row"><div class="field wide">Message</div></div>
    <button class="submit" type="button">SUBMIT</button>
  </form>
</section>

<footer class="site-footer">
  <nav class="footer-nav">
    <span>Home</span><span>|</span><span>About Us</span><span>|</span><span>Services</span><span>|</span><span>Gallery</span><span>|</span><span>Testimonials</span><span>|</span><span>Events</span><span>|</span><span>Check Availability</span><span>|</span><span>Contact Us</span>
  </nav>
  <p class="copyright">Copyright &copy; 2017 Maple Lantern Productions. All rights reserved.</p>
  <div class="social"><span></span><span></span><span></span><span></span></div>
</footer>

</body>
</html>
```